Etiketten für Olivenöl-Intensivcreme
Zielgruppe
Wir produzieren Bio-Food, u.a. Wein und Olivenöl. Jetzt soll eine Olivenöl-Intensivcreme im Bereich Kosmetik auf dem Markt platziert werden. Unsere Zielgruppe hat ein sehr breites Altersspektrum (jung bis alt), ist naturverbunden, tierlieb, gebildet, kritisch-reflektierend, weiß gute Qualität zu schätzen, ist überwiegend weiblich. Die Olivenöl-Intensivcreme hat eine sehr breite Verwendung und soll sich als 'Allzweckwaffe' in jedem Haushalt etablieren (Babyhaut-Pflege, Lippenpflege, Ganzkörperpflege, Hand-Schutzcreme etc.).
Aufgabenstellung
Die Creme soll heißen: Velamira (es könnte z.B. der Buchstabe 'O' durch eine Olive ersetzt werden). Es gibt zwei Etikette (Deckeloberseite der Metalldose und auf dem Boden). Der Durchmesser der Etikette ist jeweils 5,5 cm. Die Deckelunterseite gilt reinen Pflichtangaben. Im Dateidownloadbereich sind die Textvorgaben für die Etikette. MUT zur Farbe! Wir sind NICHT brav und angepasst! Orange kann Akzente setzen bzw. für Aufmerksamkeit im Regal sorgen.

```html
<!DOCTYPE html>
<html lang="de">
<head>
<meta charset="utf-8">
<title>Velamira – Deckeletikett</title>
<link rel="stylesheet" href="https://fonts.googleapis.com/css2?family=Amatic+SC:wght@700&family=Kreon:wght@500&display=swap">
<style>
  :root {
    --stage: #ffffff;
    --rim: #c9c9c9;
    --label-orange: #ef8152;
    --ink: #1e1a18;
    --paper: #ffffff;
    --leaf-tone: #f6e9df;
  }
  * { margin: 0; padding: 0; box-sizing: border-box; }
  html, body {
    width: 1200px; height: 1160px; overflow: hidden;
    background: var(--stage);
  }
  .canvas {
    position: relative; width: 1200px; height: 1160px;
  }
  .label {
    position: absolute; left: 90px; top: 70px;
    width: 1020px; height: 1020px; border-radius: 50%;
    background: var(--label-orange);
    border: 10px solid var(--rim);
    overflow: hidden;
  }
  .brand {
    position: absolute; left: 0; right: 0; top: 225px;
    display: flex; justify-content: center; align-items: center; gap: 16px;
    font-family: "Amatic SC", cursive; font-weight: 700;
    font-size: 66px; letter-spacing: 2px; color: var(--paper);
  }
  .brand-dot {
    width: 22px; height: 22px; border-radius: 50%; background: var(--paper);
  }
  .branch-art {
    position: absolute; left: 40px; top: 330px; width: 300px; height: 180px;
  }
  .badge {
    position: absolute; left: 650px; top: 285px;
    width: 230px; height: 230px; border-radius: 50%;
    background: var(--ink); color: var(--paper);
    display: flex; flex-direction: column; justify-content: center; align-items: center;
    font-family: "Amatic SC", cursive; font-weight: 700;
    font-size: 62px; line-height: 0.95; text-align: center;
  }
  .product-name {
    position: absolute; left: 0; right: 0; top: 455px;
    padding-left: 150px; text-align: center;
    font-family: "Kreon", serif; font-weight: 500;
    font-size: 176px; line-height: 1; letter-spacing: -2px; color: var(--paper);
  }
  .product-type {
    position: absolute; left: 0; right: 0; top: 640px;
    text-align: center;
    font-family: "Amatic SC", cursive; font-weight: 700;
    font-size: 96px; line-height: 1; color: var(--ink);
  }
  .claims {
    position: absolute; left: 0; right: 0; top: 750px;
    display: flex; flex-direction: column; align-items: center; gap: 4px;
  }
  .claim {
    background: var(--ink); color: var(--paper);
    font-family: "Amatic SC", cursive; font-weight: 700;
    font-size: 70px; line-height: 1; padding: 4px 40px;
  }
  .claim--first { transform: rotate(-3deg); margin-left: 20px; }
  .claim--second { transform: rotate(-3deg); margin-left: 60px; }
</style>
</head>
<body>
<main class="canvas">
  <section class="label">
    <div class="brand"><span class="brand-dot"></span><span>VERANO.HOF</span></div>

    <svg class="branch-art" viewBox="0 0 300 180" role="img" aria-label="Gezeichneter Olivenzweig mit zwei Blättern">
      <rect x="0" y="0" width="300" height="180" rx="20" fill="var(--leaf-tone)" opacity="0.55"/>
    </svg>

    <div class="badge"><span>NATUR-</span><span>KOSMETIK</span></div>

    <h1 class="product-name">velamira</h1>
    <p class="product-type">OLIVENÖL-INTENSIVCREME</p>

    <div class="claims">
      <span class="claim claim--first">BIO-OLIVE + VEGAN</span>
      <span class="claim claim--second">PFLEGE- UND SCHUTZCREME</span>
    </div>
  </section>
</main>
</body>
</html>
```